Vibrant, yet professional, stationery set and other designs required.

I need to source a fantastic designer for a new project as part of my company using a new logo designed via sketch harbor.

**UPDATE** I am not looking for just 'fine' design that will suffice. I am looking for something great.

We are a life assurance brokerage based in Dublin, Ireland and BrightRoost.ie is our new website aimed at providing services for young families in Ireland. We are hoping to be the 'Velro' level of service providers in this area and I am looking for the quality of design to reflect this :-) Hopefully that makes sense!

I have a preference for straight lines over curves and waves.

I need...

1. Business card
2. Letterhead
3. Banner (for printing - 76cm X 305cm)
4. Car branding for KORVA 9 (2014 sport model) I believe the templates are freely available online.

Target Market(s)

Parents in Ireland - Aged 27 to 50.

Industry/Entity Type

Financial Planning

Colors

Designer to choose colors to be used in the design.

Requirements
Must have
• All of the items listed in the description above. I like clean, bright, legible, vibrant and professional design.
Should not have
• No silly or 'cheap' looking designs. This is a professional company looking to provide a professional service.

```html
<!DOCTYPE html>
<html lang="en">
<head>
<meta charset="utf-8">
<title>BrightRoost.ie Business Card</title>
<link href="https://fonts.googleapis.com/css2?family=Roboto:wght@400;500&family=Roboto+Condensed:wght@400;500&display=swap" rel="stylesheet">
<style>
  :root {
    --backdrop: #e4e4e3;
    --card-white: #f7f7f6;
    --brand-grey: #8c999d;
    --brand-green: #8dc63f;
    --text-dark: #4a4a4a;
    --text-muted: #8a8f92;
    --rule: #c9cccd;
    --white: #ffffff;
  }
  * { box-sizing: border-box; margin: 0; padding: 0; }
  html, body { width: 1200px; height: 960px; overflow: hidden; }
  body {
    position: relative;
    background: var(--backdrop);
    font-family: "Roboto", Arial, sans-serif;
  }
  .card {
    position: absolute;
    width: 601px;
    height: 342px;
  }
  .card-front { left: 302px; top: 130px; background: var(--card-white); }
  .card-back { left: 299px; top: 489px; background: var(--brand-grey); }

  .brand {
    position: absolute;
    display: flex;
    align-items: center;
    gap: 10px;
    font-family: "Roboto", Arial, sans-serif;
    font-weight: 500;
    white-space: nowrap;
  }
  .brand-dot { border-radius: 50%; flex: none; }
  .card-front .brand {
    right: 34px; top: 180px;
    font-size: 42px; color: var(--brand-grey);
    letter-spacing: -0.5px;
  }
  .card-front .brand-dot { width: 18px; height: 18px; background: var(--brand-green); }
  .card-back .brand {
    left: 50%; top: 50%; transform: translate(-50%, -50%);
    font-size: 60px; color: var(--white);
    letter-spacing: -0.5px;
  }
  .card-back .brand-dot { width: 24px; height: 24px; background: var(--white); }

  .holder-name {
    position: absolute; left: 28px; top: 174px;
    font-family: "Roboto Condensed", Arial, sans-serif;
    font-weight: 500; font-size: 23px; color: var(--brand-green);
  }
  .holder-role {
    position: absolute; left: 28px; top: 200px;
    font-family: "Roboto Condensed", Arial, sans-serif;
    font-size: 16px; color: var(--text-muted);
  }
  .divider {
    position: absolute; left: 28px; right: 35px; top: 226px;
    height: 1px; background: var(--rule);
  }
  .contact-list {
    position: absolute; left: 30px; top: 239px;
    list-style: none;
    font-size: 14.5px; color: var(--text-dark);
  }
  .contact-list li {
    display: flex; align-items: center; gap: 9px;
    height: 19px;
  }
  .contact-icon { width: 12px; height: 12px; fill: var(--brand-green); flex: none; }
  .address {
    position: absolute; right: 32px; top: 256px;
    text-align: right; font-style: normal;
    font-size: 14.5px; line-height: 19px; color: var(--text-dark);
  }
</style>
</head>
<body>
  <section class="card card-front">
    <div class="brand"><span class="brand-dot"></span>BrightRoost.ie</div>

    <h1 class="holder-name">LIAM CARTER</h1>
    <p class="holder-role">CEO/FOUNDER</p>
    <div class="divider"></div>

    <ul class="contact-list">
      <li>
        <svg class="contact-icon" viewBox="0 0 12 12"><path d="M2.5 0.5l2 2.2-1.1 1.4c.7 1.6 2 2.9 3.5 3.6l1.4-1.1 2.2 2-1.2 2C5 10.3 1.6 7 .5 1.7z"/></svg>
        614 205 7781
      </li>
      <li>
        <svg class="contact-icon" viewBox="0 0 12 12"><path d="M3 0h6v12H3zM4 1.5v8h4v-8zM5.5 10.3h1v1h-1z" fill-rule="evenodd"/></svg>
        852 319 4607
      </li>
      <li>
        <svg class="contact-icon" viewBox="0 0 12 12"><path d="M3 0h6v3H3zM0 4h12v6H10v2H2v-2H0zM3 8v3h6V8z" fill-rule="evenodd"/></svg>
        473 560 2198
      </li>
      <li>
        <svg class="contact-icon" viewBox="0 0 12 12"><path d="M0 2h12v8H0zM1 3l5 3.5L11 3z" fill-rule="evenodd"/></svg>
        liam@brightroost.com
      </li>
    </ul>

    <address class="address">
      2146 Larchwood Row<br>
      Fairmont, Oregon 58213<br>
      www.brightroost.com
    </address>
  </section>

  <section class="card card-back">
    <div class="brand"><span class="brand-dot"></span>BrightRoost.ie</div>
  </section>
</body>
</html>
```